Business Card for a Dental Office

The design should communicate integrity, quality and reliability. We also want the card look elegant, simple, but still stand out, different from the traditional-dental-office business card.

Industry/Entity Type

Business

```html
<!DOCTYPE html>
<html lang="en">
<head>
<meta charset="utf-8">
<title>Corbell Dental Centre – Business Card</title>
<link rel="stylesheet" href="https://fonts.googleapis.com/css2?family=Oswald:wght@500;600&family=Open+Sans:wght@400;600;700&display=swap">
<style>
  :root {
    --backdrop: #d9d4cb;
    --card-black: #0c0c0c;
    --card-sheen: #262626;
    --accent-lime: #c8d422;
    --accent-gold: #c9b43c;
    --text-white: #f4f4f4;
    --text-soft: #d8d8d8;
  }
  * { box-sizing: border-box; margin: 0; padding: 0; }
  html, body { width: 1200px; height: 1022px; overflow: hidden; }
  body {
    background: var(--backdrop);
    font-family: "Open Sans", Arial, sans-serif;
    position: relative;
  }
  .card {
    position: absolute;
    left: 280px;
    width: 640px;
    height: 366px;
    background: linear-gradient(160deg, var(--card-sheen) 0%, var(--card-black) 45%, var(--card-black) 100%);
    box-shadow: 0 14px 30px rgba(0,0,0,0.35);
    overflow: hidden;
  }
  .card--front { top: 110px; }
  .card--back { top: 546px; }

  /* Front */
  .brand {
    position: absolute;
    left: 44px;
    top: 62px;
    display: flex;
    align-items: center;
    gap: 14px;
  }
  .brand__square {
    width: 46px;
    height: 46px;
    background: var(--accent-lime);
  }
  .brand__name {
    font-family: "Oswald", "Arial Narrow", sans-serif;
    font-weight: 600;
    font-size: 34px;
    letter-spacing: 0.5px;
    line-height: 1;
    color: var(--text-white);
    text-transform: uppercase;
  }
  .brand__tagline {
    margin-top: 5px;
    font-weight: 700;
    font-size: 12.5px;
    letter-spacing: 1.6px;
    color: var(--accent-gold);
    text-transform: uppercase;
  }
  .person {
    position: absolute;
    right: 44px;
    top: 168px;
    text-align: right;
  }
  .person__name {
    font-family: "Oswald", "Arial Narrow", sans-serif;
    font-weight: 500;
    font-size: 28px;
    letter-spacing: 1.5px;
    color: var(--text-white);
    text-transform: uppercase;
    line-height: 1.1;
  }
  .person__title {
    font-size: 12px;
    letter-spacing: 2.5px;
    color: var(--accent-gold);
    text-transform: uppercase;
  }
  .divider {
    position: absolute;
    left: 44px;
    right: 44px;
    top: 236px;
    height: 2px;
    background: var(--accent-lime);
  }
  .contacts {
    position: absolute;
    left: 44px;
    list-style: none;
  }
  .card--front .contacts { top: 252px; }
  .contacts__item {
    display: flex;
    align-items: center;
    gap: 10px;
    font-size: 15px;
    line-height: 27px;
    color: var(--text-soft);
  }
  .contacts__icon { width: 13px; height: 13px; flex: none; }

  /* Back */
  .card--back .band {
    position: absolute;
    right: 0;
    top: 0;
    width: 28px;
    height: 100%;
    background: var(--accent-lime);
  }
  .card--back .person { top: 70px; right: 76px; }
  .card--back .person__rule {
    margin-top: 8px;
    margin-left: auto;
    width: 210px;
    height: 2px;
    background: var(--accent-lime);
  }
  .card--back .contacts {
    top: 230px;
    padding-left: 16px;
    border-left: 2px solid var(--accent-lime);
  }
</style>
</head>
<body>

<section class="card card--front" aria-label="Business card front">
  <div class="brand">
    <div class="brand__square"></div>
    <div>
      <div class="brand__name">Corbell Dental Centre</div>
      <div class="brand__tagline">Careful hands for a lasting smile</div>
    </div>
  </div>

  <div class="person">
    <div class="person__name">Marek Olsen</div>
    <div class="person__title">Director</div>
  </div>

  <div class="divider"></div>

  <ul class="contacts">
    <li class="contacts__item">
      <svg class="contacts__icon" viewBox="0 0 16 16"><path d="M3 1.5l3 3-1.6 1.8a9 9 0 0 0 5.3 5.3L11.5 10l3 3-2 2C6.5 14.5 1.5 9.5 1 3.5z" fill="none" stroke="#c8d422" stroke-width="1.4" stroke-linejoin="round"/></svg>
      +330 5712-4093
    </li>
    <li class="contacts__item">
      <svg class="contacts__icon" viewBox="0 0 16 16"><rect x="1" y="3" width="14" height="10" fill="none" stroke="#c8d422" stroke-width="1.4"/><path d="M1 3l7 6 7-6" fill="none" stroke="#c8d422" stroke-width="1.4"/></svg>
      info@corbelldentalcentre.com
    </li>
    <li class="contacts__item">
      <svg class="contacts__icon" viewBox="0 0 16 16"><circle cx="8" cy="8" r="6.5" fill="none" stroke="#c8d422" stroke-width="1.4"/><path d="M1.5 8h13M8 1.5c-3 3.5-3 9.5 0 13M8 1.5c3 3.5 3 9.5 0 13" fill="none" stroke="#c8d422" stroke-width="1.2"/></svg>
      www.corbelldentalcentre.com
    </li>
  </ul>
</section>

<section class="card card--back" aria-label="Business card back">
  <div class="band"></div>

  <div class="person">
    <div class="person__name">Marek Olsen</div>
    <div class="person__title">Director</div>
    <div class="person__rule"></div>
  </div>

  <ul class="contacts">
    <li class="contacts__item">
      <svg class="contacts__icon" viewBox="0 0 16 16"><path d="M3 1.5l3 3-1.6 1.8a9 9 0 0 0 5.3 5.3L11.5 10l3 3-2 2C6.5 14.5 1.5 9.5 1 3.5z" fill="none" stroke="#c8d422" stroke-width="1.4" stroke-linejoin="round"/></svg>
      +330 5712-4093
    </li>
    <li class="contacts__item">
      <svg class="contacts__icon" viewBox="0 0 16 16"><rect x="1" y="3" width="14" height="10" fill="none" stroke="#c8d422" stroke-width="1.4"/><path d="M1 3l7 6 7-6" fill="none" stroke="#c8d422" stroke-width="1.4"/></svg>
      info@corbelldentalcentre.com
    </li>
    <li class="contacts__item">
      <svg class="contacts__icon" viewBox="0 0 16 16"><circle cx="8" cy="8" r="6.5" fill="none" stroke="#c8d422" stroke-width="1.4"/><path d="M1.5 8h13M8 1.5c-3 3.5-3 9.5 0 13M8 1.5c3 3.5 3 9.5 0 13" fill="none" stroke="#c8d422" stroke-width="1.2"/></svg>
      www.corbelldentalcentre.com
    </li>
  </ul>
</section>

</body>
</html>
```